Business Card Design

Just looking for a good designs that looks good with our company logo. I'd like it to be simple and to the point. Just including contact information, our logo, and my name somewhere on the card so future clients know who they're contacting, and a couple services offered. The two images I attached are pictures of our logo. I don't care which color they they are, I just attached both images to give a reference of logo colors depending on the color of the card.
Names: Carl Whitby
Phone: 816-555-0147
Email: greenstripeyard@fernmail.test
Services offered:
Mowing
Fertilization
Aeration
Bed & tree maintenance
and more.
Business
Names: Carl Whitby
Phone: 816-555-0147
(no website)

```html
<!DOCTYPE html>
<html lang="en">
<head>
<meta charset="utf-8">
<title>Greenstripe Yard – Business Card</title>
<link rel="stylesheet" href="https://fonts.googleapis.com/css2?family=Open+Sans:wght@400;600;700&display=swap">
<style>
  :root {
    --coral: #e4523d;
    --navy: #353944;
    --paper: #ffffff;
    --backdrop: #e8e5e1;
  }
  * { box-sizing: border-box; margin: 0; padding: 0; }
  html, body {
    width: 1200px; height: 959px; overflow: hidden;
    background: var(--backdrop);
    font-family: "Open Sans", Arial, sans-serif;
  }
  .card {
    position: absolute; left: 100px; top: 195px;
    width: 1000px; height: 570px;
    background: var(--paper);
    box-shadow: 0 18px 40px rgba(0,0,0,.18);
  }
  .top-bar { position: absolute; top: 0; height: 12px; background: var(--coral); }
  .top-bar--left { left: 0; width: 333px; }
  .top-bar--middle { left: 333px; width: 334px; height: 18px; background: var(--navy); }
  .top-bar--right { left: 667px; width: 333px; }

  .brand {
    position: absolute; top: 58px; left: 0; right: 0;
    display: flex; justify-content: center; align-items: center; gap: 14px;
  }
  .brand__dot { width: 34px; height: 34px; border-radius: 50%; background: var(--coral); }
  .brand__name {
    font-weight: 700; font-size: 40px; letter-spacing: 2px; color: var(--navy);
  }
  .person {
    position: absolute; top: 150px; left: 0; right: 0; text-align: center;
    color: var(--coral); text-transform: uppercase;
  }
  .person__name { font-size: 38px; font-weight: 400; letter-spacing: .5px; line-height: 1.15; }
  .person__title { font-size: 27px; font-weight: 400; line-height: 1.3; }

  .info {
    position: absolute; bottom: 20px; width: 312px;
    display: flex; flex-direction: column; align-items: center;
    color: var(--paper); font-size: 20px; line-height: 1.4; text-align: center;
    list-style: none;
  }
  .info--phone { left: 20px; top: 330px; background: var(--coral); padding-top: 34px; }
  .info--services { left: 344px; top: 275px; background: var(--navy); padding-top: 28px; font-size: 18px; line-height: 1.35; }
  .info--email { left: 668px; top: 215px; background: var(--coral); padding-top: 36px; font-size: 18px; }
  .info__icon { width: 58px; height: 58px; margin-bottom: 22px; }
  .info--services .info__icon { margin-bottom: 16px; }
</style>
</head>
<body>
  <main class="card">
    <div class="top-bar top-bar--left"></div>
    <div class="top-bar top-bar--middle"></div>
    <div class="top-bar top-bar--right"></div>

    <header class="brand">
      <span class="brand__dot"></span>
      <span class="brand__name">GREENSTRIPE YARD</span>
    </header>

    <section class="person">
      <h1 class="person__name">Carl Whitby</h1>
      <p class="person__title">General Manager</p>
    </section>

    <section class="info info--phone">
      <svg class="info__icon" viewBox="0 0 58 58" aria-hidden="true">
        <circle cx="29" cy="29" r="27" fill="none" stroke="#fff" stroke-width="2.5"/>
        <path d="M22 16c2 0 3 5 4 7 0 2-3 3-2 5 1 3 4 6 7 7 2 1 3-2 5-2 2 1 7 2 7 4 0 3-3 5-6 5-10-1-19-10-20-20 0-3 2-6 5-6z" fill="#fff"/>
      </svg>
      <p>816-555-0147</p>
    </section>

    <section class="info info--services">
      <svg class="info__icon" viewBox="0 0 58 58" aria-hidden="true">
        <circle cx="29" cy="29" r="27" fill="none" stroke="#fff" stroke-width="2.5"/>
        <path d="M18 30l8 8 15-17" fill="none" stroke="#fff" stroke-width="4" stroke-linecap="round" stroke-linejoin="round"/>
      </svg>
      <ul class="services-list" style="list-style:none">
        <li>Mowing</li>
        <li>Fertilization</li>
        <li>Aeration</li>
        <li>Bed &amp; tree maintenance</li>
        <li>and more.</li>
      </ul>
    </section>

    <section class="info info--email">
      <svg class="info__icon" viewBox="0 0 58 58" aria-hidden="true">
        <circle cx="29" cy="29" r="27" fill="none" stroke="#fff" stroke-width="2.5"/>
        <g fill="none" stroke="#fff" stroke-width="2.5" stroke-linejoin="round">
          <rect x="15" y="19" width="28" height="20" rx="2"/>
          <path d="M15 21l14 10 14-10"/>
        </g>
      </svg>
      <p>greenstripeyard@fernmail.test</p>
    </section>
  </main>
</body>
</html>
```